I need a business card design for a new business based in South West Australia.
I specialize in residential window cleaning & general handyman maintenance.

Dale Marsh - 412 SILVER HAWK DETAILING
- Window Cleaning
- House Maintenance

```html
<!DOCTYPE html>
<html lang="en">
<head>
<meta charset="utf-8">
<title>412 Silver Hawk Detailing – Business Card</title>
<link rel="stylesheet" href="https://fonts.googleapis.com/css2?family=Inter:wght@500&family=Libre+Bodoni:wght@700&display=swap">
<style>
  :root {
    --page-bg: #ecebe8;
    --card-white: #ffffff;
    --brand-blue: #0a6db8;
    --ink: #111111;
    --photo-sky: #f3f4f5;
    --photo-siding: #a9aca9;
    --photo-garden: #6f7d55;
  }
  html, body {
    margin: 0;
    padding: 0;
    width: 1189px;
    height: 1200px;
    overflow: hidden;
    background: var(--page-bg);
  }
  .business-card {
    position: absolute;
    left: 44px;
    top: 286px;
    width: 1100px;
    height: 628px;
    background: var(--card-white);
    box-shadow: 0 2px 6px rgba(0,0,0,0.15);
  }
  .business-card svg {
    display: block;
    width: 100%;
    height: 100%;
  }
  .company-name {
    font-family: "Inter", "Arial", sans-serif;
    font-weight: 500;
    font-size: 50px;
    fill: var(--ink);
  }
  .owner-name {
    font-family: "Libre Bodoni", "Bodoni Moda", serif;
    font-weight: 700;
    font-size: 54px;
    fill: var(--card-white);
  }
  .service-item {
    font-family: "Inter", "Arial", sans-serif;
    font-weight: 500;
    font-size: 37px;
    fill: var(--card-white);
  }
  .service-bullet circle,
  .service-bullet line {
    stroke: #e8eef8;
    fill: none;
    stroke-width: 2;
  }
  .service-bullet .bullet-core {
    fill: #ffffff;
    stroke: none;
  }
</style>
</head>
<body>
  <div class="business-card">
    <svg viewBox="0 0 1123 641" xmlns="http://www.w3.org/2000/svg">
      <defs>
        <linearGradient id="house-photo-tones" x1="0" y1="0" x2="0" y2="1">
          <stop offset="0" stop-color="var(--photo-sky)"/>
          <stop offset="0.22" stop-color="#d6d7d6"/>
          <stop offset="0.6" stop-color="var(--photo-siding)"/>
          <stop offset="0.88" stop-color="#8f948c"/>
          <stop offset="1" stop-color="var(--photo-garden)"/>
        </linearGradient>
      </defs>

      <polygon class="house-photo" role="img"
               aria-label="Photo of a two-storey house with a magnifying glass enlarging an upper window"
               points="0,0 315,0 552,320 318,641 0,641"
               fill="url(#house-photo-tones)"/>

      <line class="accent-stripe" x1="330" y1="0" x2="572" y2="322"
            stroke="var(--brand-blue)" stroke-width="7"/>

      <polygon class="contact-band" points="581,320 1123,320 1123,641 336,641"
               fill="var(--brand-blue)"/>

      <text class="company-name" text-anchor="end" x="1073" y="147">412 SILVER HAWK</text>
      <text class="company-name" text-anchor="end" x="1073" y="209">DETAILING</text>

      <text class="owner-name" text-anchor="end" x="1073" y="415">Dale Marsh</text>

      <text class="service-item" text-anchor="end" x="1003" y="524">Window Cleaning</text>
      <text class="service-item" text-anchor="end" x="1003" y="590">House Maintenance</text>

      <g class="service-bullet" transform="translate(1052 512)">
        <circle r="12"/>
        <line x1="-17" y1="0" x2="17" y2="0"/>
        <line x1="0" y1="-17" x2="0" y2="17"/>
        <circle class="bullet-core" r="4.5"/>
      </g>
      <g class="service-bullet" transform="translate(1052 577)">
        <circle r="12"/>
        <line x1="-17" y1="0" x2="17" y2="0"/>
        <line x1="0" y1="-17" x2="0" y2="17"/>
        <circle class="bullet-core" r="4.5"/>
      </g>
    </svg>
  </div>
</body>
</html>
```